Website for IT consulting Company

I need a website upgrade, the existing site content is ok, I would also like to add a testimonial page, the site should be something that is easy for us to update content. You use the content from www.kelvanbrook.com as an example. I will also post update logo and artwork. I also need a contact form with some type of validation or captcha.

I added Coded to the Project

Please omit Address maps

Target Market(s)

small business, service oriented companies. We provide IT Consulting, support and mangement

Industry/Entity Type

Information Technology

Coding

Number of Pages Required

1 page

Font styles to use
Serif
Sans Serif

Requirements
Must have
• Contain logo attached, and content from existing web site www.kelvanbrook.com.
• Also need to update content easily, and be movable to different platforms.
• There is a catch phrase
• "Let us worry about your technology…” “ so you don’t have to!”
• Should be included.
Nice to have
• Testimonial page, Project page where we can post new and past projects and pictures
Should not have
• none

```html
<!DOCTYPE html>
<html lang="en">
<head>
<meta charset="utf-8">
<title>Kelvanbrook – IT Solutions</title>
<link href="https://fonts.googleapis.com/css2?family=Roboto:wght@400;500;700&family=Roboto+Condensed:wght@700&family=Lato:wght@400;700&display=swap" rel="stylesheet">
<style>
:root{
  --blue:#1e9ad6;
  --blue-dark:#147bb0;
  --ink:#1a1a1a;
  --grey-text:#7a7a7a;
  --dark-card:#3b3b3b;
  --band:#f1f1f3;
  --line:#2b2b2b;
  --footer:#050505;
  --white:#ffffff;
}
*{margin:0;padding:0;box-sizing:border-box}
html,body{width:1200px;height:3020px;overflow:hidden}
body{position:relative;font-family:"Lato",Arial,sans-serif;color:var(--ink);background:var(--white)}

/* hero */
.hero{position:absolute;left:0;top:0;width:1200px;height:695px;overflow:hidden}
.hero-art{position:absolute;inset:0;background:radial-gradient(ellipse at 55% 40%,#2a8db5 0%,#0f5c82 40%,#082f4a 100%)}
.brand{position:absolute;left:40px;top:38px;display:flex;align-items:center;gap:12px;color:var(--white);font-family:"Roboto",Arial,sans-serif;font-weight:700;font-size:40px;letter-spacing:1px}
.brand-mark{width:44px;height:44px;background:var(--blue);border-radius:6px}
.nav{position:absolute;top:50px;left:470px;display:flex;font-family:"Roboto",Arial,sans-serif;font-size:18px;color:#dbe9f2}
.nav a{color:inherit;text-decoration:none;margin-right:42px}
.nav a.active{color:var(--white);font-weight:700}
.hero-title{position:absolute;top:292px;left:0;width:1200px;text-align:center;font-family:"Roboto Condensed",Arial,sans-serif;font-weight:700;font-size:48px;color:var(--white);letter-spacing:.5px}
.hero-text{position:absolute;top:364px;left:80px;width:1040px;text-align:center;font-size:18px;line-height:30px;color:#eef5fa}
.btn{display:inline-block;background:var(--blue);color:var(--white);border-radius:5px;text-align:center;font-family:"Roboto",Arial,sans-serif}
.hero-btn{position:absolute;left:535px;top:459px;width:124px;height:42px;line-height:42px;font-size:18px}
.hero-dots{position:absolute;top:642px;left:528px;display:flex;gap:12px}
.hero-dots span{width:16px;height:16px;border:2px solid #cfe3ef;border-radius:3px}
.hero-dots span.on{background:var(--blue);border-color:var(--blue)}

/* section heading */
.sec-title{position:absolute;left:0;width:1200px;text-align:center;font-family:"Roboto",Arial,sans-serif;font-weight:700;font-size:32px;color:var(--ink)}
.sec-rule{position:absolute;width:220px;height:14px}
.sec-rule::before{content:"";position:absolute;left:0;right:0;top:6px;height:2px;background:var(--line)}
.sec-rule::after{content:"";position:absolute;left:103px;top:0;width:14px;height:14px;background:var(--line)}
.sec-rule.light::before,.sec-rule.light::after{background:var(--white)}

/* services */
.service{position:absolute;top:856px;width:270px;height:192px;border:3px solid var(--dark-card);border-radius:10px;background:var(--white)}
.service.featured{border-color:var(--blue)}
.service-icon{position:absolute;top:-50px;left:-34px;width:110px;height:110px;background:var(--dark-card);border-radius:12px;display:flex;align-items:center;justify-content:center}
.service.featured .service-icon{background:var(--blue)}
.service-name{position:absolute;left:92px;top:12px;font-family:"Roboto",Arial,sans-serif;font-size:17px;line-height:18px;color:var(--ink)}
.service-text{position:absolute;left:46px;top:90px;width:208px;font-size:14px;line-height:24px;color:#333}

/* support band */
.support{position:absolute;left:0;top:1101px;width:1200px;height:522px;background:var(--band)}
.support-photo{position:absolute;left:0;top:0;width:540px;height:522px;background:linear-gradient(120deg,#d8e3ea 0%,#9fb8c6 45%,#c9d6dd 100%)}
.support-item{position:absolute;width:320px;height:70px}
.support-ico{position:absolute;left:0;top:0;width:70px;height:70px;border:2px solid var(--dark-card);border-radius:50%;display:flex;align-items:center;justify-content:center;background:var(--white)}
.support-item.featured .support-ico{background:var(--blue);border-color:var(--blue)}
.support-name{position:absolute;left:88px;top:2px;font-family:"Roboto",Arial,sans-serif;font-size:17px;color:#333;white-space:nowrap}
.support-item.featured .support-name{color:var(--blue)}
.support-text{position:absolute;left:88px;top:25px;width:180px;font-size:14px;line-height:19px;color:#444}

/* about */
.about-photo{position:absolute;left:700px;top:1670px;width:500px;height:365px;background:linear-gradient(90deg,#ffffff 0%,#e9ecef 30%,#b8bfc6 100%)}
.about-text{position:absolute;left:38px;width:690px;font-size:14px;line-height:28px;color:var(--grey-text)}
.about-text b{color:var(--ink);font-weight:700}
.about-btn{position:absolute;left:38px;top:2005px;width:105px;height:36px;line-height:36px;font-size:15px}

/* testimonials */
.testimonials{position:absolute;left:0;top:2088px;width:1200px;height:460px;background:linear-gradient(180deg,#0d0d0d 0%,#1b1e22 50%,#0d0d0d 100%)}
.quote-mark{position:absolute;left:0;width:1200px;text-align:center;font-family:Georgia,serif;font-size:70px;color:var(--white);line-height:1}
.testimonial-text{position:absolute;left:90px;top:2288px;width:1020px;text-align:center;font-size:17px;line-height:29px;color:#b9b9b9}
.testimonial-name{position:absolute;left:0;top:2436px;width:1200px;text-align:center;font-family:"Roboto",Arial,sans-serif;font-weight:500;font-size:18px;color:var(--white)}
.testimonial-name i{font-style:normal;color:var(--blue)}
.t-dots{position:absolute;top:2483px;left:563px;display:flex;gap:8px}
.t-dots span{width:11px;height:11px;border:2px solid var(--blue);transform:rotate(45deg)}

/* contact */
.field{position:absolute;border:1px solid #b5b5b5;font-size:14px;color:#555;padding:10px 14px;background:var(--white)}
.submit{position:absolute;left:970px;top:2700px;width:106px;height:108px;background:linear-gradient(180deg,#3fb0e6,var(--blue-dark));color:var(--white);font-family:"Roboto",Arial,sans-serif;font-weight:700;font-size:20px;display:flex;align-items:center;justify-content:center;border:1px solid var(--blue-dark)}

/* footer */
.footer{position:absolute;left:0;top:2835px;width:1200px;height:185px;background:var(--footer)}
.social{position:absolute;top:2868px;left:487px;display:flex;gap:8px}
.social span{width:30px;height:30px;background:#5a5a5a;border-radius:3px}
.social span:first-child{background:var(--blue)}
.footer-links{position:absolute;top:2928px;left:0;width:1200px;text-align:center;font-size:14px;color:#ccc}
.footer-links b{color:var(--white)}
.copyright{position:absolute;top:2954px;left:0;width:1200px;text-align:center;font-size:14px;color:#aaa}
.copyright b{color:var(--white)}
</style>
</head>
<body>

<header class="hero">
  <div class="hero-art" role="img" aria-label="Businesswoman touching a digital interface over a glowing blue world map"></div>
  <div class="brand"><span class="brand-mark"></span>Kelvanbrook</div>
  <nav class="nav">
    <a class="active">Home</a><a>About</a><a>Supports</a><a>Clients</a><a>Projects</a><a>Careers</a><a>Contact</a>
  </nav>
  <h1 class="hero-title">IT SOLUTIONS THAT WORK FOR YOUR BUSINESS</h1>
  <p class="hero-text">Kelvanbrook is a technology solution provider based in Houston, Texas. Our goal is to make technology a non-issue for individuals and small to medium size businesses ranging from 5 to 150 Users. Kelvanbrook has the experience, the tools, high-level technology</p>
  <span class="btn hero-btn">Read More</span>
  <div class="hero-dots"><span class="on"></span><span></span><span></span><span></span><span></span></div>
</header>

<h2 class="sec-title" style="top:732px">WHAT WE&nbsp; DO</h2>
<div class="sec-rule" style="left:490px;top:781px"></div>

<div class="service featured" style="left:72px">
  <div class="service-icon">
    <svg width="64" height="56" viewBox="0 0 64 56" fill="none" stroke="#fff" stroke-width="5"><circle cx="22" cy="22" r="12"/><circle cx="46" cy="40" r="8"/><circle cx="22" cy="22" r="3" fill="#fff"/></svg>
  </div>
  <div class="service-name">Managed IT<br>Solutions</div>
  <p class="service-text">Our staff will design, service, administer and maintain your IT needs. We are well versed on all major operating...</p>
</div>
<div class="service" style="left:372px">
  <div class="service-icon">
    <svg width="60" height="60" viewBox="0 0 60 60" fill="#fff"><circle cx="26" cy="14" r="10"/><path d="M8 48c0-12 8-20 18-20s18 8 18 20z"/><rect x="32" y="34" width="24" height="16" rx="2" stroke="#3b3b3b" stroke-width="2"/></svg>
  </div>
  <div class="service-name">Remote<br>Diagnostic<br>&amp; Support</div>
  <p class="service-text">Do you need a quick solution to a technical problem? With our live remote -assistance tool...</p>
</div>
<div class="service" style="left:645px">
  <div class="service-icon">
    <svg width="60" height="56" viewBox="0 0 60 56" fill="none" stroke="#fff" stroke-width="3"><rect x="6" y="4" width="26" height="34" rx="2"/><line x1="11" y1="12" x2="27" y2="12"/><line x1="11" y1="20" x2="27" y2="20"/><rect x="26" y="24" width="28" height="20" rx="2"/><line x1="34" y1="50" x2="46" y2="50"/></svg>
  </div>
  <div class="service-name">Hosting<br>and<br>Virtulization</div>
  <p class="service-text">Lorem ipsum dolor sitet, consectetur adipiscingit. Quisque pulvinar pretium interdumuisque coallis...</p>
</div>
<div class="service" style="left:918px">
  <div class="service-icon">
    <svg width="60" height="60" viewBox="0 0 60 60" fill="none" stroke="#fff" stroke-width="3"><circle cx="20" cy="14" r="8"/><rect x="22" y="26" width="32" height="22" rx="2"/><line x1="30" y1="42" x2="46" y2="30"/><line x1="32" y1="54" x2="44" y2="54"/></svg>
  </div>
  <div class="service-name">IT<br>Infrastructure<br>Design &amp;<br>Installation</div>
  <p class="service-text" style="top:94px">Do you need a quick solution to a technical problem? With our live remote-assistanc tool, a member of our support...</p>
</div>

<section class="support">
  <div class="support-photo" role="img" aria-label="Two colleagues working together at a laptop in a bright office"></div>
</section>
<h2 class="sec-title" style="top:1140px;left:510px;width:600px">IT SUPPORT SOLUTIONS</h2>
<div class="sec-rule" style="left:700px;top:1189px"></div>

<div class="support-item featured" style="left:543px;top:1220px">
  <div class="support-ico"><svg width="34" height="34" viewBox="0 0 34 34" fill="#fff" stroke="#fff" stroke-width="2"><circle cx="17" cy="17" r="4"/><circle cx="17" cy="4" r="3"/><circle cx="5" cy="26" r="3"/><circle cx="29" cy="26" r="3"/><line x1="17" y1="7" x2="17" y2="13"/><line x1="7" y1="24" x2="14" y2="19"/><line x1="27" y1="24" x2="20" y2="19"/></svg></div>
  <div class="support-name">Network Adminstration</div>
  <div class="support-text">risus nec commodo porttitor, arcu ipsum imperdiet lacus,</div>
</div>
<div class="support-item" style="left:888px;top:1220px">
  <div class="support-ico"><svg width="34" height="30" viewBox="0 0 34 30" fill="none" stroke="#333" stroke-width="2.5"><rect x="3" y="4" width="10" height="20"/><rect x="16" y="8" width="16" height="12"/><line x1="20" y1="26" x2="28" y2="26"/></svg></div>
  <div class="support-name">Desktop Support</div>
  <div class="support-text">Praesent consecteturant siut neque luctusnec luc</div>
</div>
<div class="support-item" style="left:543px;top:1313px">
  <div class="support-ico"><svg width="30" height="34" viewBox="0 0 30 34" fill="none" stroke="#333" stroke-width="2.5"><rect x="3" y="4" width="8" height="10"/><rect x="19" y="20" width="8" height="10"/><path d="M7 14v6q0 8 8 8h4"/></svg></div>
  <div class="support-name">Netwrok Cabling</div>
  <div class="support-text">Asrit consectetur tellus nunc vitae lacusliquam phare</div>
</div>
<div class="support-item" style="left:888px;top:1313px">
  <div class="support-ico"><svg width="34" height="28" viewBox="0 0 34 28" fill="none" stroke="#333" stroke-width="2.5"><path d="M3 10a20 20 0 0 1 28 0"/><path d="M8 15a13 13 0 0 1 18 0"/><path d="M13 20a6 6 0 0 1 8 0"/><circle cx="17" cy="24" r="1.5" fill="#333"/></svg></div>
  <div class="support-name">Wireless Network</div>
  <div class="support-text">Tus massa pulvinaraece nasnisl neque elementu</div>
</div>
<div class="support-item" style="left:543px;top:1406px">
  <div class="support-ico"><svg width="32" height="30" viewBox="0 0 32 30" fill="none" stroke="#333" stroke-width="2.5"><rect x="3" y="6" width="8" height="20"/><rect x="13" y="10" width="16" height="16"/><line x1="17" y1="15" x2="25" y2="15"/><line x1="17" y1="20" x2="25" y2="20"/></svg></div>
  <div class="support-name">Telecommunications</div>
  <div class="support-text">tra nisi enim, vitae interdum nisl euismod euusce utneque</div>
</div>
<div class="support-item" style="left:888px;top:1406px">
  <div class="support-ico"><svg width="28" height="32" viewBox="0 0 28 32" fill="none" stroke="#333" stroke-width="2.5"><path d="M14 3l10 4v9c0 7-5 11-10 13C9 27 4 23 4 16V7z"/><path d="M14 6v20"/></svg></div>
  <div class="support-name">Antivirus Soultions</div>
  <div class="support-text">Smet massa euursus vrr ipsum Vivamus vehicula</div>
</div>
<div class="support-item" style="left:543px;top:1496px">
  <div class="support-ico"><svg width="32" height="32" viewBox="0 0 32 32" fill="none" stroke="#333" stroke-width="2.5"><circle cx="16" cy="16" r="12"/><circle cx="16" cy="16" r="5"/><line x1="7" y1="7" x2="12" y2="12"/><line x1="25" y1="25" x2="20" y2="20"/><line x1="25" y1="7" x2="20" y2="12"/><line x1="7" y1="25" x2="12" y2="20"/></svg></div>
  <div class="support-name">Disaster Recovery</div>
  <div class="support-text">ipsum. Vestibulum a augue nisi. Nulla luctus leo mi,</div>
</div>
<div class="support-item" style="left:888px;top:1496px">
  <div class="support-ico"><svg width="34" height="30" viewBox="0 0 34 30" fill="none" stroke="#333" stroke-width="2.5"><rect x="3" y="4" width="28" height="18" rx="1"/><line x1="11" y1="27" x2="23" y2="27"/><path d="M12 10l-3 3 3 3M22 10l3 3-3 3"/></svg></div>
  <div class="support-name">Web Design</div>
  <div class="support-text">Bibendum augue ac laci sagittis accums pulvinar</div>
</div>

<div class="about-photo" role="img" aria-label="Businesswoman with a coffee cup working at a laptop"></div>
<h2 class="sec-title" style="top:1662px;left:290px;width:600px">ABOUT US</h2>
<div class="sec-rule" style="left:480px;top:1711px"></div>
<p class="about-text" style="top:1730px"><b>Outsourcing</b> is subcontracting a process, such as product design or manufacturing, to a third-party company. The decision to outsource is often made in the interest of lowering firm costs, redirecting or conserving energy directed at the competencies of a particular business, or to make more efficient use of land, labor, capital, (information) technology and resources.&nbsp;&nbsp;&nbsp; Outsourcing became part of the business lexicon during the 1980s.</p>
<p class="about-text" style="top:1878px">Kelvanbrook is a technology solution provider based in Houston, Texas. Our goal is to make technology a non-issue for individuals and small to medium size businesses ranging from 5 to 150 Users. Kelvanbrook has the experience, the tools, high-level technology solutions and training to power your business and your work force. We understand that all business's have one goal in common!</p>
<span class="btn about-btn">Read More</span>

<section class="testimonials" role="img" aria-label="Dim photo of business people in an office"></section>
<h2 class="sec-title" style="top:2128px;color:#fff">TESTIMONIALS</h2>
<div class="sec-rule light" style="left:490px;top:2177px"></div>
<div class="quote-mark" style="top:2236px">&ldquo;</div>
<p class="testimonial-text">We are extremely happy with our frank, open, and honest relationship with Northgate Partners. Northgate Partners' solution and delivery capabilities in the technology business not only improved the time to market and predictability, but reduced the cost of implementation</p>
<div class="quote-mark" style="top:2376px;font-size:56px;color:#aaa">&rdquo;</div>
<div class="testimonial-name">Lorem ipsum <i>|</i> Company Name</div>
<div class="t-dots"><span></span><span></span><span></span><span></span></div>

<h2 class="sec-title" style="top:2605px">CONTACT US</h2>
<div class="sec-rule" style="left:490px;top:2654px"></div>
<div class="field" style="left:120px;top:2700px;width:258px;height:45px">First Name:</div>
<div class="field" style="left:396px;top:2700px;width:260px;height:45px">Last Name:</div>
<div class="field" style="left:672px;top:2700px;width:280px;height:108px">Comments:</div>
<div class="field" style="left:120px;top:2763px;width:258px;height:45px">Phone:</div>
<div class="field" style="left:396px;top:2763px;width:260px;height:45px">Email:</div>
<div class="submit">SUBMIT</div>

<footer class="footer"></footer>
<div class="social"><span></span><span></span><span></span><span></span><span></span><span></span></div>
<div class="footer-links"><b>Home</b>&nbsp; / &nbsp;About Us&nbsp; / &nbsp;Supports&nbsp; / &nbsp;Client&nbsp; / &nbsp;Careers&nbsp; / Contact</div>
<div class="copyright">© 2017. <b>kelvanbrook</b>.All Rights Reserved.</div>

</body>
</html>
```